BOLD & MINIMALIST DESIGN NEEDED

We want a very bold but minimalistic business card design that is impactful and utilizes both sides of the business card. Our current logo is included for your use.

We want bold fonts and good use of negative space. We don't want the logo to overpower the design.

Target Market(s)

Professionals who are building new commercial buildings.

Industry/Entity Type

Construction

Contact Information for Business Card

Name, Title, email, office phone, cell phone, website

Font styles to use
Serif
Sans Serif

Requirements
Must have
• Bold design!

```html
<!DOCTYPE html>
<html lang="en">
<head>
<meta charset="UTF-8">
<title>Summit Ridge Design + Build — Business Card</title>
<link rel="stylesheet" href="https://fonts.googleapis.com/css2?family=Oswald:wght@300;700&family=Montserrat:wght@400&display=swap">
<style>
  :root {
    --stage: #141414;
    --card: #1c1c1c;
    --card-edge: #262626;
    --green: #7ac231;
    --white: #ffffff;
    --muted: #d9d9d9;
  }
  * { box-sizing: border-box; margin: 0; padding: 0; }
  html, body {
    width: 1200px; height: 900px; overflow: hidden;
    background: var(--stage);
  }
  .canvas {
    width: 1200px; height: 900px;
    display: flex; flex-direction: column; align-items: center; justify-content: center;
    gap: 40px;
  }
  .card {
    position: relative;
    width: 700px; height: 400px;
    border-radius: 22px;
    background: var(--card);
    overflow: hidden;
    box-shadow: 0 18px 40px rgba(0,0,0,.55);
  }
  .brand-name {
    font-family: "Oswald", sans-serif;
    font-weight: 700;
    color: var(--white);
    text-transform: uppercase;
    line-height: 1;
  }
  .brand-mark {
    display: inline-block; width: 22px; height: 22px;
    background: var(--green);
    margin-right: 12px;
  }

  /* Front */
  .front .brand {
    position: absolute; left: 150px; top: 48px;
    display: flex; align-items: center;
  }
  .front .brand-name .main { display: block; font-size: 40px; letter-spacing: 1px; }
  .front .brand-name .sub { display: block; font-size: 16px; letter-spacing: 6px; margin-top: 6px; }
  .front .accent-line {
    position: absolute; left: 60px; top: 168px;
    width: 560px; height: 2px; background: var(--green);
  }
  .contact {
    position: absolute; left: 44px; top: 190px;
    list-style: none;
    font-family: "Montserrat", sans-serif; font-size: 17px; color: var(--white);
  }
  .contact li { display: flex; align-items: center; gap: 10px; margin-bottom: 6px; }
  .contact svg { width: 16px; height: 16px; flex: none; }
  .person {
    position: absolute; right: 46px; top: 206px; text-align: right;
  }
  .person-name {
    font-family: "Oswald", sans-serif; font-weight: 700;
    font-size: 50px; color: var(--green); text-transform: uppercase; line-height: 1;
    letter-spacing: .5px;
  }
  .person-title {
    font-family: "Montserrat", sans-serif; font-size: 17px; color: var(--white);
    letter-spacing: 2px; margin-top: 8px;
    border-top: 2px solid var(--green); padding-top: 4px; display: inline-block;
  }
  .bottom-bands { position: absolute; left: 0; bottom: 0; width: 700px; height: 58px; }
  .website {
    position: absolute; right: 52px; bottom: 14px;
    font-family: "Montserrat", sans-serif; font-size: 19px; color: var(--white);
    letter-spacing: 1px;
  }

  /* Back */
  .back .pattern {
    position: absolute; inset: 0;
    background: radial-gradient(ellipse at 30% 30%, #2a2a2a 0%, #1e1e1e 55%, #171717 100%);
  }
  .back .brand {
    position: absolute; right: 70px; top: 150px;
    display: flex; align-items: center;
  }
  .back .brand-name .main { display: block; font-size: 48px; letter-spacing: 1px; }
  .back .brand-name .sub { display: block; font-size: 18px; letter-spacing: 8px; margin-top: 6px; }
</style>
</head>
<body>
<main class="canvas">

  <section class="card front" aria-label="Business card front">
    <div class="brand">
      <span class="brand-mark"></span>
      <p class="brand-name"><span class="main">Summit Ridge</span><span class="sub">Design + Build</span></p>
    </div>
    <div class="accent-line"></div>

    <ul class="contact">
      <li>
        <svg viewBox="0 0 24 24" aria-hidden="true"><path fill="#7ac231" d="M6.6 10.8a15 15 0 0 0 6.6 6.6l2.2-2.2a1 1 0 0 1 1-.25 11.4 11.4 0 0 0 3.6.57 1 1 0 0 1 1 1V20a1 1 0 0 1-1 1A17 17 0 0 1 3 4a1 1 0 0 1 1-1h3.5a1 1 0 0 1 1 1c0 1.25.2 2.45.57 3.57a1 1 0 0 1-.25 1z"/></svg>
        (555) 014-2276
      </li>
      <li>
        <svg viewBox="0 0 24 24" aria-hidden="true"><rect x="3" y="9" width="18" height="12" rx="2" fill="#7ac231"/><path d="M2 8c3-4 17-4 20 0l-3 2-2-2H7l-2 2z" fill="#7ac231"/><circle cx="12" cy="15" r="3" fill="#1c1c1c"/></svg>
        (555) 014-2277
      </li>
      <li>
        <svg viewBox="0 0 24 24" aria-hidden="true"><rect x="2.5" y="5.5" width="19" height="13" fill="none" stroke="#7ac231" stroke-width="2"/><path d="M3 6l9 7 9-7" fill="none" stroke="#7ac231" stroke-width="2"/></svg>
        summitridgebuild@mail.com
      </li>
    </ul>

    <div class="person">
      <p class="person-name">Marcus Hale</p>
      <p class="person-title">OWNER</p>
    </div>

    <svg class="bottom-bands" viewBox="0 0 700 58" aria-hidden="true">
      <rect x="0" y="38" width="380" height="10" fill="#ffffff"/>
      <polygon points="395,0 700,0 700,58 360,58" fill="#7ac231"/>
    </svg>
    <p class="website">www.summitridgebuild.com</p>
  </section>

  <section class="card back" aria-label="Business card back">
    <div class="pattern" role="img" aria-label="Faint repeating brand-symbol pattern in dark grey tones across the card"></div>
    <div class="brand">
      <span class="brand-mark"></span>
      <p class="brand-name"><span class="main">Summit Ridge</span><span class="sub">Design + Build</span></p>
    </div>
  </section>

</main>
</body>
</html>
```